IT Company that provides secure IT solutions and services to our customers

We need business cards and a logo for a new IT Solutions company just created based in Kuala Lumpur, Malaysia. But will also be serving other countries in the region. We provide secure data, voice solutions on mobile platforms. Our first offering is encrypted voice and data solutions for IOS, Android, Windows and BlackBerry devices.

Target Market(s)

large organizations Govt, Police, Defence, Anti-corruption, Legal, highly regulated industries such as Health-care, Financial, Banking, Insurance,

Industry/Entity Type

Information Technology

Contact Information for Business Card

VelmoraNet (Logo - colour is ORVEX blue)Roshan Adeel Managing Director Kryption IT Sdn. Bhd.5th Floor, Block D, Wisma PLB,No.14 Jalan Seri Melor,50470, Kuala LumpurMalaysia

Font styles to use
Sans Serif

Colors
3176b5
ec1f27
fbed22

Requirements
Must have
• VelmoraNet all in Blue like ORVEX blue. A logo design perhaps a play of VN, K with a dangling T (colour can be any)
Nice to have
• I want a clean crisp card, not too busy, easy to read.

```html
<!DOCTYPE html>
<html lang="en">
<head>
<meta charset="utf-8">
<title>VelmoraNet Business Card</title>
<link rel="stylesheet" href="https://fonts.googleapis.com/css2?family=PT+Sans:wght@400;700&display=swap">
<style>
  :root {
    --backdrop: #000000;
    --card: #323335;
    --brand-red: #d2302f;
    --brand-blue: #2466b4;
    --ink-light: #f2f2f2;
    --divider: #4a3a3a;
  }
  * { margin: 0; padding: 0; box-sizing: border-box; }
  html, body {
    width: 1200px; height: 900px; overflow: hidden;
    background: var(--backdrop);
    font-family: "PT Sans", "Myriad Pro", sans-serif;
  }
  .canvas { position: relative; width: 1200px; height: 900px; }
  .card {
    position: absolute; top: 271px;
    width: 457px; height: 281px;
    background: var(--card);
    border-radius: 14px;
  }
  .card--front { left: 137px; }
  .card--back { left: 626px; }

  .brand-mark {
    position: absolute; left: 54px; top: 87px;
    width: 107px; height: 107px; border-radius: 50%;
    background: var(--brand-red);
  }
  .divider {
    position: absolute; left: 191px; top: 91px;
    width: 1px; height: 80px; background: var(--divider);
  }
  .contact { position: absolute; left: 212px; top: 74px; color: var(--ink-light); }
  .person-name { font-size: 15px; font-weight: 700; color: var(--brand-red); line-height: 18px; }
  .person-role { font-size: 13px; line-height: 16px; }
  .company { margin-top: 31px; margin-left: 2px; }
  .company-name { font-size: 15px; font-weight: 700; color: var(--brand-red); line-height: 18px; }
  .company-address { font-size: 13px; line-height: 16.5px; font-style: normal; }

  .wordmark {
    position: absolute; left: 0; right: 0; top: 100px;
    text-align: center;
    font-size: 50px; font-weight: 700; color: var(--brand-blue);
    letter-spacing: -0.5px;
  }
</style>
</head>
<body>
<main class="canvas">
  <section class="card card--front" aria-label="Card front">
    <div class="brand-mark" aria-hidden="true"></div>
    <div class="divider" aria-hidden="true"></div>
    <div class="contact">
      <p class="person-name">Roshan Adeel</p>
      <p class="person-role">Managing Director</p>
      <div class="company">
        <p class="company-name">Velmora Net</p>
        <address class="company-address">
          Sdn. Bhd.5th Floor, Block D,<br>
          Wisma PLB,No.14 Jalan Seri Melor,<br>
          50470, Kuala Lumpur<br>
          Malaysia
        </address>
      </div>
    </div>
  </section>

  <section class="card card--back" aria-label="Card back">
    <p class="wordmark">VelmoraNet</p>
  </section>
</main>
</body>
</html>
```